Business Management Fortress

Assist with enhancing a powerpoint slide by providing a few design options for consideration. I have a template but open to any creative ideas.

Internal employees and stakeholders

Business Management, Finance, Accounting

• Maintain a fortress, temple, or pyramid schema
• Scenic Background

```html
<!DOCTYPE html>
<html lang="en">
<head>
<meta charset="utf-8">
<title>Business Management Fortress</title>
<link rel="stylesheet" href="https://fonts.googleapis.com/css2?family=Oswald:wght@600;700&family=Source+Sans+3:wght@400;500&display=swap">
<style>
  :root {
    --bg-light: #f1f1f1;
    --bg-mist: #dcdcdc;
    --brown: #8c6a5b;
    --brown-dark: #5b4036;
    --brown-shadow: #6e5044;
    --white: #ffffff;
    --dash: #8c6a5b;

    --yellow: #f2b81c;
    --yellow-mid: #f4cf5e;
    --yellow-light: #f3d47a;

    --blue: #366e9c;
    --blue-mid: #6a9bc0;
    --blue-light: #9dc6e2;

    --red: #8b0a0a;
    --red-mid: #e8222e;
    --red-light: #f2a8ae;

    --green: #4c7a22;
    --green-mid: #8dc63f;
    --green-light: #cfe3a8;
  }
  html, body {
    margin: 0;
    padding: 0;
    width: 1200px;
    height: 656px;
    overflow: hidden;
    background: var(--bg-light);
  }
  .slide {
    position: relative;
    width: 1200px;
    height: 656px;
    overflow: hidden;
  }
  .scenic-backdrop {
    position: absolute;
    inset: 0;
    background:
      radial-gradient(ellipse 40% 45% at 8% 45%, rgba(150,150,150,0.45), transparent 70%),
      radial-gradient(ellipse 35% 40% at 94% 40%, rgba(160,160,160,0.4), transparent 70%),
      linear-gradient(180deg, #f4f4f4 0%, #e6e6e6 55%, #d9d9d9 80%, #e9e9e9 100%);
  }
  .fortress {
    position: absolute;
    inset: 0;
  }
  .roof-label {
    font-family: "Oswald", sans-serif;
    font-weight: 700;
    fill: var(--white);
    letter-spacing: 0.5px;
  }
  .pillar-label {
    font-family: "Oswald", sans-serif;
    font-weight: 600;
    font-size: 12.5px;
    fill: var(--white);
    text-anchor: middle;
    letter-spacing: 0.3px;
  }
  .foundation-title {
    font-family: "Oswald", sans-serif;
    font-weight: 700;
    font-size: 30px;
    fill: var(--white);
    text-anchor: middle;
    letter-spacing: -0.3px;
  }
  .foundation-duties {
    font-family: "Source Sans 3", sans-serif;
    font-weight: 500;
    font-size: 13.5px;
    fill: var(--white);
    text-anchor: middle;
  }
  .pillar-ghost { opacity: 0.22; }
</style>
</head>
<body>
<div class="slide">
  <div class="scenic-backdrop" role="img" aria-label="Faded snowy mountain landscape"></div>

  <svg class="fortress" width="1200" height="656" viewBox="0 0 1200 656" xmlns="http://www.w3.org/2000/svg">
    <defs>
      <linearGradient id="photo-leader" x1="0" y1="0" x2="1" y2="1">
        <stop offset="0" stop-color="#8a6a58"/>
        <stop offset="0.6" stop-color="#5a3e32"/>
        <stop offset="1" stop-color="#2e2420"/>
      </linearGradient>
      <linearGradient id="photo-partner" x1="0" y1="0" x2="0" y2="1">
        <stop offset="0" stop-color="#6b5a52"/>
        <stop offset="0.5" stop-color="#b79c8c"/>
        <stop offset="1" stop-color="#3c3d4a"/>
      </linearGradient>
      <linearGradient id="photo-profit" x1="0" y1="0" x2="1" y2="1">
        <stop offset="0" stop-color="#c07a3e"/>
        <stop offset="0.5" stop-color="#7a4a2a"/>
        <stop offset="1" stop-color="#3a2518"/>
      </linearGradient>
      <linearGradient id="foundation-fill" x1="0" y1="0" x2="1" y2="1">
        <stop offset="0" stop-color="#8a6a5b"/>
        <stop offset="1" stop-color="#8f6e5f"/>
      </linearGradient>
    </defs>

    <!-- Roof -->
    <g class="roof">
      <polygon points="169,197 408,28 647,197" fill="url(#photo-leader)" stroke="var(--brown-dark)" stroke-width="4" stroke-linejoin="round" role="img" aria-label="Photo of a cheering businesswoman"/>
      <polygon points="556,197 796,28 1035,197" fill="url(#photo-profit)" stroke="var(--brown-dark)" stroke-width="4" stroke-linejoin="round" role="img" aria-label="Photo of a magnifying glass over financial charts"/>
      <polygon points="356,197 596,28 835,197" fill="url(#photo-partner)" stroke="var(--brown-dark)" stroke-width="4" stroke-linejoin="round" role="img" aria-label="Photo of a smiling professional offering a handshake"/>
      <text class="roof-label" font-size="22" transform="translate(318 177) rotate(-52)">LEADER</text>
      <text class="roof-label" font-size="22" x="599" y="162" text-anchor="middle">PARTNER</text>
      <text class="roof-label" font-size="22" transform="translate(780 92) rotate(46)">PROFITABILITY</text>
    </g>

    <!-- Beam -->
    <rect class="beam" x="162" y="197" width="877" height="17" rx="8.5" fill="var(--brown)"/>

    <!-- Ghost pillars -->
    <g class="pillar-ghost">
      <g transform="translate(370 0)">
        <rect x="-34" y="227" width="68" height="12" fill="var(--yellow-light)"/>
        <rect x="-27" y="239" width="54" height="13" fill="var(--yellow-light)"/>
        <rect x="-18.5" y="252" width="37" height="204" fill="var(--yellow-light)"/>
        <rect x="-27" y="456" width="54" height="13" fill="var(--yellow-light)"/>
        <rect x="-34" y="469" width="68" height="12" fill="var(--yellow-light)"/>
      </g>
      <g transform="translate(606 0)">
        <rect x="-34" y="227" width="68" height="12" fill="var(--blue-light)"/>
        <rect x="-27" y="239" width="54" height="13" fill="var(--blue-light)"/>
        <rect x="-18.5" y="252" width="37" height="204" fill="var(--blue-light)"/>
        <rect x="-27" y="456" width="54" height="13" fill="var(--blue-light)"/>
        <rect x="-34" y="469" width="68" height="12" fill="var(--blue-light)"/>
      </g>
      <g transform="translate(841 0)">
        <rect x="-34" y="227" width="68" height="12" fill="var(--red-light)"/>
        <rect x="-27" y="239" width="54" height="13" fill="var(--red-light)"/>
        <rect x="-18.5" y="252" width="37" height="204" fill="var(--red-light)"/>
        <rect x="-27" y="456" width="54" height="13" fill="var(--red-light)"/>
        <rect x="-34" y="469" width="68" height="12" fill="var(--red-light)"/>
      </g>
    </g>

    <!-- Connecting line -->
    <line x1="300" y1="358" x2="903" y2="358" stroke="var(--dash)" stroke-width="1.6" stroke-dasharray="5 3"/>

    <!-- Pillar: People -->
    <g class="pillar pillar-people" transform="translate(245 0)">
      <rect x="-34" y="227" width="68" height="12" fill="var(--yellow)"/>
      <rect x="-27" y="239" width="54" height="13" fill="var(--yellow-light)"/>
      <rect x="-18.5" y="252" width="37" height="204" fill="var(--yellow-light)"/>
      <rect x="-27" y="456" width="54" height="13" fill="var(--yellow-light)"/>
      <rect x="-34" y="469" width="68" height="12" fill="var(--yellow)"/>
      <rect x="-55.5" y="298" width="111" height="113" rx="10" fill="var(--yellow)"/>
      <circle cx="0" cy="337" r="21" fill="var(--white)"/>
      <g fill="var(--yellow)">
        <circle cx="-8" cy="330" r="4"/>
        <circle cx="8" cy="330" r="4"/>
        <circle cx="0" cy="334" r="4.5"/>
        <path d="M-15 345 a7 6 0 0 1 14 0 z"/>
        <path d="M1 345 a7 6 0 0 1 14 0 z"/>
        <path d="M-8 348 a8 7 0 0 1 16 0 z"/>
      </g>
      <text class="pillar-label" x="0" y="381">PEOPLE</text>
    </g>

    <!-- Pillar: Innovation -->
    <g class="pillar pillar-innovation" transform="translate(482 0)">
      <rect x="-34" y="227" width="68" height="12" fill="var(--blue)"/>
      <rect x="-27" y="239" width="54" height="13" fill="var(--blue-mid)"/>
      <rect x="-18.5" y="252" width="37" height="204" fill="var(--blue-light)"/>
      <rect x="-27" y="456" width="54" height="13" fill="var(--blue-mid)"/>
      <rect x="-34" y="469" width="68" height="12" fill="var(--blue)"/>
      <rect x="-55.5" y="298" width="111" height="113" rx="10" fill="var(--blue)"/>
      <circle cx="0" cy="337" r="21" fill="var(--white)"/>
      <g fill="var(--blue)">
        <path d="M0 324 a9 9 0 0 1 5.5 16 v3 h-11 v-3 A9 9 0 0 1 0 324 z"/>
        <rect x="-4.5" y="344.5" width="9" height="2.5" rx="1"/>
        <rect x="-3" y="348" width="6" height="2" rx="1"/>
      </g>
      <circle cx="0" cy="333" r="3" fill="var(--white)"/>
      <text class="pillar-label" x="0" y="381">INNOVATION</text>
    </g>

    <!-- Pillar: Business Intelligence -->
    <g class="pillar pillar-intelligence" transform="translate(719 0)">
      <rect x="-34" y="227" width="68" height="12" fill="var(--red)"/>
      <rect x="-27" y="239" width="54" height="13" fill="var(--red-mid)"/>
      <rect x="-18.5" y="252" width="37" height="204" fill="var(--red-light)"/>
      <rect x="-27" y="456" width="54" height="13" fill="var(--red-mid)"/>
      <rect x="-34" y="469" width="68" height="12" fill="var(--red)"/>
      <rect x="-55.5" y="298" width="111" height="113" rx="10" fill="var(--red)"/>
      <circle cx="0" cy="337" r="21" fill="var(--white)"/>
      <g fill="var(--red)">
        <path d="M-4.5 330 v-3 h9 v3 h-2 v-1.4 h-5 v1.4 z"/>
        <rect x="-12" y="330" width="24" height="16" rx="2"/>
      </g>
      <rect x="-12" y="336.5" width="24" height="1.4" fill="var(--white)"/>
      <rect x="-2" y="335" width="4" height="4" fill="var(--white)"/>
      <text class="pillar-label" x="0" y="381">BUSINESS</text>
      <text class="pillar-label" x="0" y="396">INTELLIGENCE</text>
    </g>

    <!-- Pillar: Strategic Alliances -->
    <g class="pillar pillar-alliances" transform="translate(955 0)">
      <rect x="-34" y="227" width="68" height="12" fill="var(--green)"/>
      <rect x="-27" y="239" width="54" height="13" fill="var(--green-mid)"/>
      <rect x="-18.5" y="252" width="37" height="204" fill="var(--green-light)"/>
      <rect x="-27" y="456" width="54" height="13" fill="var(--green-mid)"/>
      <rect x="-34" y="469" width="68" height="12" fill="var(--green)"/>
      <rect x="-55.5" y="298" width="111" height="113" rx="10" fill="var(--green)"/>
      <circle cx="0" cy="337" r="21" fill="var(--white)"/>
      <g fill="var(--green)">
        <rect x="-12" y="326" width="24" height="16" rx="1"/>
        <rect x="-14" y="324.5" width="28" height="2.5"/>
        <path d="M-6 342 l-3 8 h2 l3 -8 z M6 342 l3 8 h-2 l-3 -8 z"/>
      </g>
      <path d="M-8 338 q5 -8 10 -3 t6 -5" fill="none" stroke="var(--white)" stroke-width="1.4" stroke-dasharray="2 1.5"/>
      <text class="pillar-label" x="0" y="381">STRATEGIC</text>
      <text class="pillar-label" x="0" y="396">ALLIANCES</text>
    </g>

    <!-- Foundation -->
    <g class="foundation">
      <path d="M161 498 h878 v100 a30 30 0 0 1 -30 30 h-818 a30 30 0 0 1 -30 -30 z" fill="var(--brown-shadow)"/>
      <path d="M161 493 h878 v98 a30 30 0 0 1 -30 30 h-818 a30 30 0 0 1 -30 -30 z" fill="url(#foundation-fill)"/>
      <text class="foundation-title" x="600" y="551">FIDUCIARY RESPONSIBILITIES</text>
      <text class="foundation-duties" x="600" y="574">ACCURATE FINANCIALS / INTERNAL CONTROLS / BRAND</text>
      <text class="foundation-duties" x="600" y="593">PROTECTION / COMPLIANCE / ETHICS / COST MANAGEMENT</text>
    </g>
  </svg>
</div>
</body>
</html>
```